New Business Card Design Project

I need a design for business cards, i am an electrical business called "Corvane Electrical and Communications" i need the cards to be double sided with the company logo on the back (attached) the front needs to say my company name, web site, email address, telephone number, and ABN number and electrical license number. I am open to different arrangements of the information but would like the background to be incorporating something electrical or something that looks smart. open to all additional ideas also.

The company colours are orange and grey see logo attached.

Business Name: Corvane Electrical and Communications
Website: corvaneelectricalandcomms.example.com.au
Email: brent@corvaneelectricalandcomms.example.com.au
Telephone(mobile): 0481209736
ABN: 71208349162
Lic No: 418273D

Target Market(s)

Business entities, Project Managers, Accounts, Clients

Industry/Entity Type

Electrician

Contact Information for Business Card

I need a design for business cards, i am an electrical business called "Corvane Electrical and Communications" i need the cards to be double sided with the company logo on the back (attached) the front needs to say my company name

Font styles to use
Serif
Sans Serif

Colors
f37122
5c5c5c

Requirements
Must have
• Must have the Logo on the back open to different ways of it being on the back but had in mind to keep it central but again open to other options
Nice to have
• A real modern cool background that is eye catching yet contemporary
Should not have
• No backgrounds of a light bulb or plug or anything like that

```html
<!DOCTYPE html>
<html lang="en">
<head>
<meta charset="utf-8">
<title>Corvane Electrical and Communications — Business Card</title>
<link href="https://fonts.googleapis.com/css2?family=Open+Sans:wght@400;600;700&display=swap" rel="stylesheet">
<style>
  :root {
    --stage: #000000;
    --card: #5a5a5b;
    --accent: #f5b324;
    --ink: #ffffff;
  }
  * { margin: 0; padding: 0; box-sizing: border-box; }
  html, body { width: 1200px; height: 900px; overflow: hidden; background: var(--stage); }
  body { position: relative; font-family: "Open Sans", sans-serif; color: var(--ink); }

  .card {
    position: absolute;
    top: 184px;
    height: 491px;
    background: var(--card);
    border-radius: 14px;
    text-align: center;
    overflow: hidden;
  }
  .card--front { left: 299px; width: 301px; }
  .card--back  { left: 645px; width: 304px; }

  .brand {
    position: absolute;
    color: var(--ink);
    font-weight: 600;
    text-align: left;
    line-height: 1;
    white-space: nowrap;
  }
  .brand__name { display: block; font-size: 40px; letter-spacing: 1px; }
  .brand__sub  { display: block; font-size: 11px; letter-spacing: 0.4px; margin-top: 8px; }
  .card--front .brand { left: 39px; top: 88px; }
  .card--back .brand  { left: 33px; top: 360px; }
  .card--back .brand .brand__name { font-size: 44px; }
  .card--back .brand .brand__sub  { font-size: 12px; }

  .brand__dot {
    display: inline-block;
    width: 11px; height: 11px;
    border-radius: 50%;
    background: var(--accent);
    margin-left: 6px;
    vertical-align: top;
    margin-top: 6px;
  }

  .person { position: absolute; left: 0; right: 0; top: 243px; }
  .person__name { color: var(--accent); font-weight: 700; font-size: 17px; line-height: 22px; }
  .person__role { font-size: 13px; line-height: 18px; }

  .details { position: absolute; left: 0; right: 0; font-size: 13px; line-height: 20px; white-space: nowrap; }
  .details--reg { top: 307px; font-weight: 600; }
  .details--contact { top: 376px; }
  .label { color: var(--accent); font-weight: 700; }
  .details--contact .is-long { font-size: 9.5px; }
  .details--contact .is-long .label { font-size: 12px; }

  .back-url {
    position: absolute;
    left: 33px;
    top: 432px;
    font-weight: 700;
    font-size: 10px;
    text-align: left;
    white-space: nowrap;
  }
</style>
</head>
<body>
  <section class="card card--front" aria-label="Business card front">
    <div class="brand">
      <span class="brand__name">CORVANE<span class="brand__dot"></span></span>
      <span class="brand__sub">ELECTRICAL AND COMMUNICATIONS</span>
    </div>

    <div class="person">
      <p class="person__name">Dale Harper</p>
      <p class="person__role">Director</p>
    </div>

    <div class="details details--reg">
      <p><span class="label">ABN:</span> 71208349162</p>
      <p><span class="label">Lic No:</span> 418273D</p>
    </div>

    <div class="details details--contact">
      <p><span class="label">Phone:</span> 0481209736</p>
      <p class="is-long"><span class="label">Email:</span> brent@corvaneelectricalandcomms.example.com.au</p>
      <p class="is-long"><span class="label">Website:</span> corvaneelectricalandcomms.example.com.au</p>
    </div>
  </section>

  <section class="card card--back" aria-label="Business card back">
    <div class="brand">
      <span class="brand__name">CORVANE<span class="brand__dot"></span></span>
      <span class="brand__sub">ELECTRICAL AND COMMUNICATIONS</span>
    </div>
    <p class="back-url">corvaneelectricalandcomms.example.com.au</p>
  </section>
</body>
</html>
```